Residential Mortgage Leader needs Wordpress Design

Looking for a home page website design for a client. We develop using the WordPress platform and would prefer the design be at least loosely based on an existing WordPress template. Attached files have many notes from our creative brief with client. The site must be responsive. Approved, basic wireframe attached. There is room for interpretation.

Existing web site: http://www.marisolkettering.example/

The Marisol Kettering Team relies on strong systems to deliver an on-time, done-right, friendly experience. Marisol offers mortgages and refinancing services throughout the United States. She is a successful Brookvale Funding agent who strives to be an active part of her community. She would like to focus the site on her team, rather than just her.

Difference makers...
When you work with the Marisol Kettering team you get a high level of expertise and a friendly experience.

She has amazing credentials. Marisol is widely recognized as a top producer for her company, and has earned a number of awards and honors for her customer service.

Marisol's team is very engaged and enjoys sharing social comments or photos from their community.

Imagery:
* Friendly, warm imagery, preferably of her team or an image to represent her team
* Clean and crisp
* Professional / Experts in mortgage and refinance
* Clean / Good use of white space
Updates

When possible, please use imagery from the DFW area. The client mentioned they would prefer not to see stock images. Thanks.

Amend that- creative use of stock images, however, is fine. A few designs have used stock imagery, but in a well-considered manner.

We added some photos and graphics that are local. We are Dallas / Ft. Worth, Plano, Frisco, Texas. We also added some examples of photos to use for the "In the Community" area. Stock photos of business folks just doesn't fit there. Thanks!

Target Market(s)

They service a lot of builders, but also work with homeowners. Their typical client is usually a woman searching for mortgage services online. She typically has a family and may refer her husband to Marisol's team. Keep in mind, however, they also see a number of other scenarios. Most of their clients are middle to high-end borrowers.

Industry/Entity Type

It Company

Requirements
Must have
• Design should be developed using program such as Photoshop or Fireworks or Illustrator as last preference. Ideally, the design would be based on an existing responsive WordPress theme, which we would customize. You must include the name of the target theme. The footer should include lots of space for disclaimers and legal language. Site navigation should include these choices: "Home, About, Builders, Mortgage Info, Approval, Blog, Contact"
Nice to have
• Blog, social media and photos area. Use of the already approved style prototype with colors and fonts (Lato- a Google font, Times New Roman and Cookie-a decorative Google font). However, we are open to interpretation.
Should not have
• Hard to read fonts or a lack of white space.

```html
<!DOCTYPE html>
<html lang="en">
<head>
<meta charset="utf-8">
<title>Brookvale Funding – Marisol Kettering Team</title>
<link href="https://fonts.googleapis.com/css2?family=Ubuntu:wght@300;400;500&display=swap" rel="stylesheet">
<style>
:root{
  --red:#c0281b;
  --red-dark:#a8190f;
  --red-light:#d6492f;
  --ink:#3b3b3b;
  --muted:#777;
  --faint:#9a9a9a;
  --hero-bg:#f1f1f1;
  --nav-top:#5b5d60;
  --nav-bot:#2e2f31;
  --footer:#39393b;
  --footer-text:#cfcfcf;
  --white:#fff;
}
*{box-sizing:border-box;margin:0;padding:0}
html,body{width:826px;height:1200px;overflow:hidden;background:var(--white)}
body{font-family:'Ubuntu',sans-serif;color:var(--ink);position:relative}
.abs{position:absolute}

/* header */
.brand{left:60px;top:30px;display:flex;align-items:center;gap:8px}
.brand-name{font-size:22px;font-weight:500;color:var(--red);letter-spacing:-.3px}
.brand-mark{width:14px;height:14px;background:var(--red)}
.brand-sub{left:61px;top:60px;font-size:11px;color:#555;font-weight:500}
.work{right:66px;top:32px;text-align:center}
.work-label{font-size:11.5px;color:#555;font-weight:300}
.work-phone{font-size:20px;color:var(--red);font-weight:500;margin-top:1px}
.work-mail{font-size:9px;color:#666;margin-top:2px}

/* nav */
.nav{left:0;top:93px;width:826px;height:35px;background:linear-gradient(var(--nav-top),var(--nav-bot));display:flex;align-items:center;padding-left:86px}
.nav a{color:var(--white);text-decoration:none;font-size:13.5px}
.nav .sep{color:#bbb;margin:0 17px;font-size:13px}

/* hero */
.hero{left:0;top:128px;width:826px;height:293px;background:var(--hero-bg)}
.hero-frame{left:62px;top:168px;width:310px;height:206px;background:var(--white);padding:6px;box-shadow:0 10px 14px -8px rgba(0,0,0,.25)}
.hero-photo{width:100%;height:100%;background:linear-gradient(135deg,#c9d9ea,#8fa8c4 55%,#2a2d34)}
.hero-title{left:398px;top:172px;font-size:37px;font-weight:300;color:#3a3a3a;letter-spacing:-.3px}
.hero-text{left:399px;top:218px;width:320px;font-size:11px;line-height:17px;color:#666;font-weight:300}
.btn{left:400px;top:298px;width:97px;height:26px;background:var(--red);color:var(--white);font-size:12px;display:flex;align-items:center;justify-content:center;box-shadow:0 1px 2px rgba(0,0,0,.3)}
.hero-or{left:512px;top:303px;font-size:11px;color:#555}
.hero-arrows{left:734px;top:384px}

/* credentials */
.creds{left:0;top:421px;width:826px;height:153px;background:linear-gradient(var(--red-light),var(--red-dark))}
.creds-divider{left:329px;top:454px;width:1px;height:90px;background:rgba(255,255,255,.18)}
.cred h2{font-weight:400;color:var(--white)}
.cred p{font-size:9px;line-height:17px;color:#f4d2cb;font-weight:300}
.cred-main{left:79px;top:448px;width:240px}
.cred-main h2{font-size:25px;margin-bottom:6px}
.cred-award{left:369px;top:455px;width:180px}
.cred-recog{left:590px;top:455px;width:180px}
.cred-award h2,.cred-recog h2{font-size:17px;margin-bottom:6px}

/* community */
.comm-title{left:0;top:615px;width:826px;text-align:center;font-size:25px;color:#3a3a3a}
.comm-sub{left:0;top:651px;width:826px;text-align:center;font-size:14px;color:#888;font-weight:300}
.section-h{font-size:17px;color:var(--red);font-weight:300}
.blog{left:70px;top:712px;width:172px}
.blog ul{list-style:none;margin-top:9px}
.blog li{font-size:10px;color:#444;height:24.5px;line-height:24px;border-bottom:1px solid #eee;padding-left:13px;position:relative}
.blog li::before{content:"";position:absolute;left:2px;top:9px;width:4px;height:4px;border-right:1px solid #aaa;border-top:1px solid #aaa;transform:rotate(45deg)}
.blog li:last-child{border-bottom:none}
.social{left:283px;top:712px;width:250px}
.post{position:absolute;left:0;display:flex;gap:9px}
.thumb{width:58px;height:47px;flex:none}
.post h3{font-size:10.5px;font-weight:400;color:#333;margin-bottom:4px}
.post p{font-size:8px;line-height:12.5px;color:#999}
.box{left:560px;top:700px;width:200px;height:217px;background:#f4f4f4;border:1px solid #e2e2e2}
.box h2{font-size:18px;font-weight:300;text-align:center;margin-top:17px;color:#444}
.people{display:grid;grid-template-columns:64px 64px;gap:12px 24px;justify-content:center;margin-top:10px}
.person{text-align:center;font-size:8px;color:#777}
.person .pic{width:63px;height:55px;background:var(--white);padding:3px;border:1px solid #e4e4e4;margin-bottom:4px}
.person .pic div{width:100%;height:100%}

/* footer */
.footer{left:0;top:958px;width:826px;height:242px;background:var(--footer);border-top:3px solid #d9d9d9}
.f-h{font-size:13.5px;color:var(--white)}
.f-col{font-size:9.5px;color:var(--footer-text);line-height:16px}
.f-contact{left:74px;top:990px}
.f-contact .org{font-size:11px;color:var(--white);margin:4px 0 1px}
.f-lang{left:255px;top:990px}
.f-lang p{line-height:16.7px}
.f-team{left:381px;top:990px}
.f-team-photo{left:382px;top:1013px;width:71px;height:71px;background:linear-gradient(#7a5a46,#c79a7e);border:1px solid #555}
.f-team-info{left:465px;top:1012px;font-size:8px;line-height:15.5px;color:var(--footer-text)}
.f-team-info .nm{font-size:11px;color:var(--white)}
.f-team-info .role{font-size:10px}
.f-touch{left:612px;top:992px}
.icons{left:612px;top:1017px;display:flex;gap:7px}
.icons span{width:17px;height:17px;display:block}
.badge{left:624px;top:1057px;width:70px;height:70px;border:3px solid #eee}
.f-rule{left:57px;top:1152px;width:712px;height:1px;background:#4a4a4c}
.copy{left:65px;top:1168px;font-size:9px;color:#8a8a8a}
</style>
</head>
<body>

<header>
  <div class="abs brand"><span class="brand-name">Brookvale Funding</span><span class="brand-mark"></span></div>
  <div class="abs brand-sub">A Harborline Capital Company</div>
  <div class="abs work">
    <div class="work-label">WORK WITH US:</div>
    <div class="work-phone">555-014-2387</div>
    <div class="work-mail">Email here</div>
  </div>
</header>

<nav class="abs nav">
  <a href="#">Home</a><span class="sep">|</span>
  <a href="#">About</a><span class="sep">|</span>
  <a href="#">Builders</a><span class="sep">|</span>
  <a href="#">Mortgage Info</a><span class="sep">|</span>
  <a href="#">Approval</a><span class="sep">|</span>
  <a href="#">Blog</a><span class="sep">|</span>
  <a href="#">Contact</a>
</nav>

<section>
  <div class="abs hero"></div>
  <div class="abs hero-frame"><div class="hero-photo" role="img" aria-label="Smiling mortgage advisor holding a white piggy bank in a bright office"></div></div>
  <h1 class="abs hero-title">Earning Your Business</h1>
  <p class="abs hero-text">Consectetuer mi, a ultricies massa est sed nisl. Class aptent taciti sociosqu ad litora torquent per conubia nostra, per inceptos hyme-naeos. Proin nulla arcu, nonummy luctus, dictum eget, fermentum et, lorem. Nunc porta convallis pede.</p>
  <div class="abs btn">Start Here</div>
  <div class="abs hero-or">-or-&nbsp; Get to Know Us</div>
  <svg class="abs hero-arrows" width="24" height="18" viewBox="0 0 24 18" fill="none" stroke="#222" stroke-width="1.8"><path d="M9 2 2 9l7 7M15 2l7 7-7 7"/></svg>
</section>

<section>
  <div class="abs creds"></div>
  <div class="abs creds-divider"></div>
  <div class="abs cred cred-main">
    <h2>Our Credentials</h2>
    <p>Consectetuer mi, a ultricies massa est sed nisl. Class aptent taciti sociosqu ad litora torquent per conubia nostra, per inceptos hymenaeos.
      <svg width="20" height="20" viewBox="0 0 20 20" style="vertical-align:middle;margin-left:6px"><circle cx="10" cy="10" r="8.5" fill="none" stroke="#fff" stroke-width="2"/><path d="M5.5 10h7M10 6.5l3.5 3.5-3.5 3.5" stroke="#fff" stroke-width="2.2" fill="none"/></svg></p>
  </div>
  <div class="abs cred cred-award">
    <h2>AWARDS</h2>
    <p>Consectetuer mi, a ultricies massa est sed nisl. Class aptent taciti sociosqu ad litora torquent per conubia nostra</p>
  </div>
  <div class="abs cred cred-recog">
    <h2>RECOGNION</h2>
    <p>Consectetuer mi, a ultricies massa est sed nisl. Class aptent taciti sociosqu ad litora torquent per conubia nostra</p>
  </div>
</section>

<section>
  <h2 class="abs comm-title" style="font-weight:400">Engaged in Our Community</h2>
  <div class="abs comm-sub">Connect with us</div>

  <div class="abs blog">
    <h3 class="section-h">BLOG POST</h3>
    <ul>
      <li>Vivamus porttitor purus</li>
      <li>Nisi eleifend libero a tempus</li>
      <li>Libero lectus feugiat</li>
      <li>Morbi diam mauris</li>
      <li>Viverra in gravida</li>
      <li>Libero lectus feugiat</li>
    </ul>
  </div>

  <div class="abs social">
    <h3 class="section-h">SOCIAL</h3>
    <div class="post" style="top:26px"><div class="thumb" role="img" aria-label="Banknotes and coins on a desk" style="background:linear-gradient(135deg,#9bb08a,#5c6e4c)"></div><div><h3>Etiam est nunc venenatis</h3><p>Class aptent taciti sociosqu ad litora torquent per conubia nostra, per inceptos</p></div></div>
    <div class="post" style="top:84px"><div class="thumb" role="img" aria-label="Hands reviewing financial charts" style="background:linear-gradient(135deg,#e6ecf2,#6d8fb3)"></div><div><h3>Mauris neque metus</h3><p>Class aptent taciti sociosqu ad litora torquent per conubia nostra hymenaeos</p></div></div>
    <div class="post" style="top:141px"><div class="thumb" role="img" aria-label="Hand holding a stack of dollar bills" style="background:linear-gradient(135deg,#c9c7bb,#7d7a68)"></div><div><h3>Curabitur iaculis</h3><p>Class aptent taciti sociosqu per conubia nostra, per inceptos hymenaeos</p></div></div>
  </div>

  <div class="abs box">
    <h2>In the Community</h2>
    <div class="people">
      <div class="person"><div class="pic"><div role="img" aria-label="Portrait of team member" style="background:linear-gradient(#a9b7c4,#5b6670)"></div></div>Name of Person</div>
      <div class="person"><div class="pic"><div role="img" aria-label="Portrait of team member" style="background:linear-gradient(#9aa5ad,#6b5a4e)"></div></div>Name of Person</div>
      <div class="person"><div class="pic"><div role="img" aria-label="Portrait of team member" style="background:linear-gradient(#e7e2dd,#4a3327)"></div></div>Name of Person</div>
      <div class="person"><div class="pic"><div role="img" aria-label="Portrait of team member" style="background:linear-gradient(#d9e2ea,#a4613b)"></div></div>Name of Person</div>
    </div>
  </div>
</section>

<footer>
  <div class="abs footer"></div>
  <div class="abs f-col f-contact">
    <div class="f-h">Contact Information</div>
    <div class="org">Brookvale Funding</div>
    <div>48 Alder Court #3B</div>
    <div>Plano 75093 TX</div>
    <div>Phone no +1 (555) 018-4420</div>
  </div>
  <div class="abs f-col f-lang">
    <div class="f-h" style="margin-bottom:3px">Language</div>
    <p>French</p><p>English</p><p>Spanish</p><p>Russian</p><p>More Language</p>
  </div>
  <div class="abs f-team f-h">Vivamus Porttitor</div>
  <div class="abs f-team-photo" role="img" aria-label="Portrait of the branch manager"></div>
  <div class="abs f-team-info">
    <div class="nm">Marisol Kettering</div>
    <div class="role">Branch Manager</div>
    <div>Office: 555.010.7731</div>
    <div>Cell: 555.019.2264</div>
    <div>mkettering@brookvale.example</div>
    <div>NMLS: 40192</div>
  </div>
  <div class="abs f-touch f-h">Get In Touch</div>
  <div class="abs icons">
    <span style="background:#3b5b98"></span>
    <span style="background:#3fa9e0"></span>
    <span style="background:#1a7ab5"></span>
    <span style="background:#f08c1e"></span>
  </div>
  <div class="abs badge"></div>
  <div class="abs f-rule"></div>
  <div class="abs copy">Copyright © 2013 Company Name.&nbsp; All right reserved</div>
</footer>

</body>
</html>
```